Velmarotix - world unique technology for better life - please let them know who am i at first sight

We need a new business card for company which is a provider of unique crystal based technology suitable for all living being. For more information and final design you can use our brochure (our colours are black and blue from brochure).
We use Verdana font

Industry/Entity Type

Business

Contact Information for Business Card

regular dimension

Font styles to use
Other font styles liked:
• Verdana

Requirements
Must have
• Logo
• name
• function/position
• phone
• mobile
• e-mail
• adress
Nice to have
• inovative design (technology directed)

```html
<!DOCTYPE html>
<html lang="en">
<head>
<meta charset="utf-8">
<title>Velmarotix Business Card</title>
<link rel="stylesheet" href="https://fonts.googleapis.com/css2?family=Open+Sans:wght@300;400;700&display=swap">
<style>
  :root {
    --page-bg: #e6dcc0;
    --card-black: #050607;
    --brand-blue: #1fa3e0;
    --band-blue: #22a7e8;
    --silver: #b9bec3;
    --text-white: #f2f4f5;
    --text-muted: #c9ced2;
  }
  * { margin: 0; padding: 0; box-sizing: border-box; }
  html, body {
    width: 1200px; height: 978px; overflow: hidden;
    background: var(--page-bg);
    font-family: "Open Sans", Verdana, sans-serif;
  }
  .sheet {
    width: 1200px; height: 978px;
    display: flex; flex-direction: column; align-items: center; justify-content: center;
    gap: 50px;
  }
  .card {
    position: relative;
    width: 760px; height: 434px;
    border-radius: 34px;
    background: var(--card-black);
    overflow: hidden;
    box-shadow: 0 10px 24px rgba(60, 45, 10, 0.25);
  }

  /* Back side */
  .card-back .brand {
    position: absolute; left: 0; right: 0; top: 150px;
    display: flex; align-items: center; justify-content: center; gap: 22px;
  }
  .brand-dot {
    width: 46px; height: 46px; border-radius: 50%;
    border: 3px solid var(--brand-blue);
  }
  .brand-name {
    color: var(--brand-blue);
    font-weight: 300;
    letter-spacing: 2px;
    line-height: 1;
  }
  .card-back .brand-name { font-size: 80px; }
  .card-back .web {
    position: absolute; left: 0; right: 0; bottom: 62px;
    text-align: center;
    color: var(--text-white);
    font-weight: 700; font-size: 19px; letter-spacing: 2px;
  }

  /* Front side */
  .card-front .band { position: absolute; inset: 0; width: 100%; height: 100%; }
  .card-front .brand {
    position: absolute; left: 230px; top: 50px;
    display: flex; align-items: center; gap: 16px;
  }
  .card-front .brand-dot { width: 38px; height: 38px; }
  .card-front .brand-name { font-size: 58px; }
  .contact {
    position: absolute; left: 112px; top: 160px;
    color: var(--text-white);
  }
  .contact .person {
    color: var(--brand-blue);
    font-weight: 700; font-size: 24px;
  }
  .contact .role { font-size: 17px; margin-bottom: 10px; color: var(--text-muted); }
  .contact .line {
    display: flex; align-items: center; gap: 18px;
    font-size: 15px; margin-top: 6px;
  }
  .contact .item { display: flex; align-items: center; gap: 6px; }
  .contact svg { width: 14px; height: 14px; fill: var(--text-white); flex: none; }
  .address {
    position: absolute; right: 44px; bottom: 28px;
    text-align: right; color: var(--text-white);
    font-size: 17px; line-height: 1.35;
  }
</style>
</head>
<body>
<main class="sheet">

  <section class="card card-back" aria-label="Card back">
    <div class="brand">
      <span class="brand-dot"></span>
      <span class="brand-name">VELMAROTIX</span>
    </div>
    <p class="web">www.velmarotix.cu</p>
  </section>

  <section class="card card-front" aria-label="Card front">
    <svg class="band" viewBox="0 0 760 434" preserveAspectRatio="none" aria-hidden="true">
      <path d="M0,70 C8,300 220,392 760,330 L760,434 L0,434 Z" fill="var(--silver)"/>
      <path d="M0,88 C14,312 230,404 760,346 L760,434 L0,434 Z" fill="var(--band-blue)"/>
    </svg>

    <div class="brand">
      <span class="brand-dot"></span>
      <span class="brand-name">VELMAROTIX</span>
    </div>

    <div class="contact">
      <p class="person">Mira Kostanic</p>
      <p class="role">Founder and CEO</p>
      <div class="line">
        <span class="item">
          <svg viewBox="0 0 16 16"><path d="M3.5 1.5l2.5 0 1 3.5-1.6 1.2a8 8 0 0 0 4.4 4.4L11 9l3.5 1v2.5A2 2 0 0 1 12.5 14.5 11 11 0 0 1 1.5 3.5 2 2 0 0 1 3.5 1.5z"/></svg>
          021-555-0147
        </span>
        <span class="item">
          <svg viewBox="0 0 16 16"><path d="M4.5 1h7a1 1 0 0 1 1 1v12a1 1 0 0 1-1 1h-7a1 1 0 0 1-1-1V2a1 1 0 0 1 1-1zm.5 2v9h6V3zm3 10a.8.8 0 1 0 0 .01z"/></svg>
          021-555-0148
        </span>
      </div>
      <div class="line">
        <span class="item">
          <svg viewBox="0 0 16 16"><path d="M1 3h14v10H1zm1.5 1.2v.3L8 8.6l5.5-4.1v-.3zm0 2.2v5.1h11V6.4L8 10.5z"/></svg>
          info@velmarotix.com
        </span>
        <span class="item">
          <svg viewBox="0 0 16 16"><path d="M8 1a7 7 0 1 0 0 14A7 7 0 0 0 8 1zm0 1.5c.7 0 1.6 1.6 1.9 4H6.1C6.4 4.1 7.3 2.5 8 2.5zM2.6 7.5h2a13 13 0 0 1 .3-3.6 5.5 5.5 0 0 0-2.3 3.6zm0 1h2a13 13 0 0 0 .3 3.6 5.5 5.5 0 0 1-2.3-3.6zm3.5 0h3.8c-.3 2.4-1.2 4-1.9 4s-1.6-1.6-1.9-4zm5.3 0h2a5.5 5.5 0 0 1-2.3 3.6 13 13 0 0 0 .3-3.6zm0-1a13 13 0 0 0-.3-3.6 5.5 5.5 0 0 1 2.3 3.6z"/></svg>
          www.velmarotix.cu
        </span>
      </div>
    </div>

    <p class="address">Street Name<br>City Name, Zipcode-01234</p>
  </section>

</main>
</body>
</html>
```